Up to the Challenge - PPT Template with Splash Slide

We are looking for a PPT template that has 4 slides.
1. Splash slide (Creative, fun, no content, a visual representation of the theme)
2. Section header slide
3. Content Slide
4. Content Slide, another design option
The theme is 'UP to the Challenge'. The design should reflect this theme.
The colors should be in Purple (#864B99), Blue (#0A80C2), and Green (#52B054).

```html
<!DOCTYPE html>
<html lang="en">
<head>
<meta charset="utf-8">
<title>Up to the Challenge – Slide Template Overview</title>
<link rel="stylesheet" href="https://fonts.googleapis.com/css2?family=Poppins:wght@600;700&family=Roboto:wght@400;500&display=swap">
<style>
  :root {
    --purple: #864B99;
    --blue: #0A80C2;
    --green: #52B054;
    --page: #bdbdbd;
    --white: #ffffff;
    --ink: #555555;
    --ink-dark: #222222;
  }
  * { margin: 0; padding: 0; box-sizing: border-box; }
  html, body { width: 1005px; height: 1200px; overflow: hidden; background: var(--page); }
  .board { position: relative; width: 1005px; height: 1200px; }

  .slide {
    position: absolute; width: 430px; height: 242px; overflow: hidden;
    background: var(--white);
    box-shadow: 0 10px 28px rgba(0,0,0,.35);
  }
  .col-a { left: 64px; }
  .col-b { left: 511px; }
  .row-1 { top: 88px; }
  .row-2 { top: 349px; }
  .row-3 { top: 610px; }
  .row-4 { top: 871px; }
  .slide.adv { left: 509px; }

  .photo { position: absolute; inset: 0; }
  .photo-purple { background: linear-gradient(120deg, #3d2f8f 0%, #6a3a98 35%, #9b4d8c 55%, #3a1d2a 75%, #140c12 100%); }
  .photo-sunset { background: linear-gradient(180deg, #a88b73 0%, #c98a45 35%, #e79a2f 52%, #1a120c 60%, #0d0907 100%); }
  .photo-night { background: linear-gradient(160deg, #0d2b66 0%, #0f4aa0 40%, #0a2d6a 70%, #07183c 100%); }
  .photo-summit { background: linear-gradient(100deg, #c9ccd0 0%, #8c9298 35%, #7b5a43 60%, #d4682a 80%, #2b1c16 100%); }
  .photo-trophy { background: linear-gradient(180deg, #8f8fa5 0%, #cfa58f 40%, #c4865a 60%, #3c2c27 100%); }
  .photo-help { background: linear-gradient(135deg, #2a2a30 0%, #6d5a4a 35%, #f0b35a 50%, #3f5a8c 70%, #2c2422 100%); }

  .hero-title {
    position: absolute; left: 30px;
    font: 700 17.5px/1 "Poppins", sans-serif; color: var(--white); letter-spacing: .1px;
  }
  .hero-date { position: absolute; left: 31px; font: 600 9px/1 "Poppins", sans-serif; }
  .date-green { color: var(--green); }
  .date-purple { color: var(--purple); }

  .section-label {
    position: absolute; left: 129px; top: 135px; width: 172px; height: 33px;
    background: var(--purple); color: var(--white);
    font: 700 18px/33px "Poppins", sans-serif; text-align: center;
  }

  .choose-ring { position: absolute; left: 14px; top: 21px; width: 200px; height: 200px; border-radius: 50%; background: rgba(210,214,218,.75); }
  .choose-disc {
    position: absolute; left: 21px; top: 28px; width: 186px; height: 186px; border-radius: 50%;
    background: var(--green); color: var(--white);
    display: flex; align-items: center; justify-content: center; text-align: center;
    font: 700 26px/1.15 "Poppins", sans-serif;
  }

  .tab {
    position: absolute; left: 0; top: 0; height: 33px; padding: 0 18px;
    background: var(--purple); color: var(--white);
    font: 700 17.5px/33px "Poppins", sans-serif; white-space: nowrap;
  }
  .tab.w-narrow { width: 125px; }
  .tab.w-wide { width: 206px; }

  .text-col { position: absolute; width: 192px; }
  .copy {
    font: 400 5.4px/9.4px "Roboto", sans-serif; color: var(--ink);
    text-align: justify; margin-bottom: 9.4px;
  }

  .checklist { position: absolute; left: 239px; top: 45px; list-style: none; }
  .checklist li {
    display: flex; align-items: center; height: 13.9px;
    font: 400 7.2px/1 "Roboto", sans-serif; color: var(--ink-dark);
  }
  .checklist svg { width: 7.5px; height: 7.5px; margin-right: 12px; flex: none; }

  .figure { position: absolute; }

  .page-no {
    position: absolute; right: 9px; bottom: 7px; width: 14px; height: 14px; border-radius: 50%;
    background: var(--blue); color: var(--white);
    font: 600 5.5px/14px "Poppins", sans-serif; text-align: center;
  }
</style>
</head>
<body>
<main class="board">

  <!-- Slide 01: splash -->
  <section class="slide col-a row-1">
    <div class="photo photo-purple" role="img" aria-label="Silhouette of a climber helping another up a rocky cliff against a purple sunset sky"></div>
    <h1 class="hero-title" style="top:131px">PRESENTATION TITLE</h1>
    <p class="hero-date date-green" style="top:162px">JUNE 13,2024</p>
    <span class="page-no">01</span>
  </section>

  <!-- Slide 05: section header -->
  <section class="slide col-b row-1">
    <div class="photo photo-sunset" role="img" aria-label="Silhouette of a person leaping across a gap between two cliffs at sunset"></div>
    <h2 class="section-label">HOW IT WORKS</h2>
    <span class="page-no">05</span>
  </section>

  <!-- Slide 02: title alternative -->
  <section class="slide col-a row-2">
    <div class="photo photo-night" role="img" aria-label="Hiker standing on a mountain peak beside a flag under a blue starry night sky"></div>
    <h1 class="hero-title" style="top:168px">PRESENTATION TITLE</h1>
    <p class="hero-date date-purple" style="top:197px">JUNE 13,2024</p>
    <span class="page-no">02</span>
  </section>

  <!-- Slide 06: section header alternative -->
  <section class="slide col-b row-2">
    <div class="photo photo-summit" role="img" aria-label="Team silhouettes pulling each other up a rocky summit at sunset"></div>
    <div class="choose-ring"></div>
    <h2 class="choose-disc">WHY<br>CHOOSE US</h2>
    <span class="page-no">06</span>
  </section>

  <!-- Slide 03: content, two columns -->
  <section class="slide col-a row-3">
    <h2 class="tab w-narrow">ABOUT US</h2>
    <div class="text-col" style="left:15px; top:45px">
      <p class="copy">Sed ut perspiciatis unde omnis iste natus error sit voluptatem accusantium doloremque laudantium, totam rem aperiam, eaque ipsa quae ab illo inventore veritatis et quasi architecto beatae vitae dicta sunt explicabo. Nemo enim ipsam voluptatem quia voluptas sit aspernatur aut odit aut fugit, sed quia consequuntur magni dolores eos qui ratione voluptatem sequi nesciunt. Neque porro quisquam est, qui dolorem ipsum quia dolor sit amet, consectetur, adipisci velit, sed quia non numquam eius modi tempora incidunt ut labore et dolore magnam aliquam quaerat voluptatem. Ut enim ad minima veniam, quis nostrum exercitationem ullam corporis suscipit laboriosam, nisi ut aliquid ex ea commodi consequatur</p>
      <p class="copy">Sed ut perspiciatis unde omnis iste natus error sit voluptatem accusantium doloremque laudantium, totam rem aperiam, eaque ipsa quae ab illo inventore veritatis et quasi architecto beatae vitae dicta sunt explicabo. Nemo enim ipsam voluptatem quia voluptas sit aspernatur aut odit aut fugit, sed quia consequuntur magni dolores eos qui ratione voluptatem sequi nesciunt. Neque porro quisquam est, qui dolorem ipsum quia dolor sit amet, consectetur, adipisci velit, sed quia non numquam eius modi tempora incidunt ut labore et dolore magnam aliquam quaerat voluptatem.</p>
    </div>
    <div class="text-col" style="left:224px; top:45px">
      <p class="copy">Sed ut perspiciatis unde omnis iste natus error sit voluptatem accusantium doloremque laudantium, totam rem aperiam, eaque ipsa quae ab illo inventore veritatis et quasi architecto beatae vitae dicta sunt explicabo. Nemo enim ipsam voluptatem quia voluptas sit aspernatur aut odit aut fugit, sed quia consequuntur magni dolores eos qui ratione voluptatem sequi nesciunt. Neque porro quisquam est, qui dolorem ipsum quia dolor sit amet, consectetur, adipisci velit, sed quia non numquam eius modi tempora incidunt ut labore et dolore magnam aliquam quaerat voluptatem. Ut enim ad minima veniam, quis nostrum exercitationem ullam corporis suscipit laboriosam, nisi ut aliquid ex ea commodi consequatur</p>
      <p class="copy">Sed ut perspiciatis unde omnis iste natus error sit voluptatem accusantium doloremque laudantium, totam rem aperiam, eaque ipsa quae ab illo inventore veritatis et quasi architecto beatae vitae dicta sunt explicabo. Nemo enim ipsam voluptatem quia voluptas sit aspernatur aut odit aut fugit, sed quia consequuntur magni dolores eos qui ratione voluptatem sequi nesciunt. Neque porro quisquam est, qui dolorem ipsum quia dolor sit amet, consectetur, adipisci velit, sed quia non numquam eius modi tempora incidunt ut labore et dolore magnam aliquam quaerat voluptatem.</p>
    </div>
    <span class="page-no">03</span>
  </section>

  <!-- Slide 07: content with image right -->
  <section class="slide adv row-3">
    <h2 class="tab w-wide">OUR ADVANTAGES</h2>
    <div class="text-col" style="left:15px; top:45px">
      <p class="copy">Sed ut perspiciatis unde omnis iste natus error sit voluptatem accusantium doloremque laudantium, totam rem aperiam, eaque ipsa quae ab illo inventore veritatis et quasi architecto beatae vitae dicta sunt explicabo. Nemo enim ipsam voluptatem quia voluptas sit aspernatur aut odit aut fugit, sed quia consequuntur magni dolores eos qui ratione voluptatem sequi nesciunt. Neque porro quisquam est, qui dolorem ipsum quia dolor sit amet, consectetur, adipisci velit, sed quia non numquam eius modi tempora incidunt ut labore et dolore magnam aliquam quaerat voluptatem. Ut enim ad minima veniam, quis nostrum exercitationem ullam corporis suscipit laboriosam, nisi ut aliquid ex ea commodi consequatur</p>
      <p class="copy">Sed ut perspiciatis unde omnis iste natus error sit voluptatem accusantium doloremque laudantium, totam rem aperiam, eaque ipsa quae ab illo inventore veritatis et quasi architecto beatae vitae dicta sunt explicabo. Nemo enim ipsam voluptatem quia voluptas sit aspernatur aut odit aut fugit, sed quia consequuntur magni dolores eos qui ratione voluptatem sequi nesciunt. Neque porro quisquam est, qui dolorem ipsum quia dolor sit amet, consectetur, adipisci velit, sed quia non numquam eius modi tempora incidunt ut labore et dolore magnam aliquam quaerat voluptatem.</p>
    </div>
    <div class="figure photo-trophy" style="left:225px; top:8px; width:192px; height:207px" role="img" aria-label="Three team silhouettes celebrating on a summit above the clouds, one raising a trophy"></div>
    <span class="page-no">07</span>
  </section>

  <!-- Slide 04: content with checklist -->
  <section class="slide col-a row-4">
    <h2 class="tab w-narrow">FEATURES</h2>
    <div class="text-col" style="left:15px; top:45px">
      <p class="copy">Sed ut perspiciatis unde omnis iste natus error sit voluptatem accusantium doloremque laudantium, totam rem aperiam, eaque ipsa quae ab illo inventore veritatis et quasi architecto beatae vitae dicta sunt explicabo. Nemo enim ipsam voluptatem quia voluptas sit aspernatur aut odit aut fugit, sed quia consequuntur magni dolores eos qui ratione voluptatem sequi nesciunt. Neque porro quisquam est, qui dolorem ipsum quia dolor sit amet, consectetur, adipisci velit, sed quia non numquam eius modi tempora incidunt ut labore et dolore magnam aliquam quaerat voluptatem. Ut enim ad minima veniam, quis nostrum exercitationem ullam corporis suscipit laboriosam, nisi ut aliquid ex ea commodi consequatur</p>
      <p class="copy">Sed ut perspiciatis unde omnis iste natus error sit voluptatem accusantium doloremque laudantium, totam rem aperiam, eaque ipsa quae ab illo inventore veritatis et quasi architecto beatae vitae dicta sunt explicabo. Nemo enim ipsam voluptatem quia voluptas sit aspernatur aut odit aut fugit, sed quia consequuntur magni dolores eos qui ratione voluptatem sequi nesciunt. Neque porro quisquam est, qui dolorem ipsum quia dolor sit amet, consectetur, adipisci velit, sed quia non numquam eius modi tempora incidunt ut labore et dolore magnam aliquam quaerat voluptatem.</p>
    </div>
    <svg width="0" height="0" style="position:absolute">
      <symbol id="tick" viewBox="0 0 16 16">
        <circle cx="8" cy="8" r="8" fill="#52B054"/>
        <path d="M4.5 8.3l2.3 2.3 4.7-4.9" fill="none" stroke="#fff" stroke-width="2" stroke-linecap="round" stroke-linejoin="round"/>
      </symbol>
    </svg>
    <ul class="checklist">
      <li><svg><use href="#tick"/></svg>Sed ut perspiciatis unde omnis iste natus</li>
      <li><svg><use href="#tick"/></svg>Eerror sit voluptatem accusantium doloremque</li>
      <li><svg><use href="#tick"/></svg>Llaudantium, totam rem aperiam, eaque ipsa</li>
      <li><svg><use href="#tick"/></svg>Quae ab illo inventore veritatis et quasi</li>
      <li><svg><use href="#tick"/></svg>Aarchitecto beatae vitae dicta sunt explicabo</li>
      <li><svg><use href="#tick"/></svg>Nemo enim ipsam voluptatem quia voluptas</li>
      <li><svg><use href="#tick"/></svg>Sit aspernatur aut odit aut fugit, sed quia</li>
      <li><svg><use href="#tick"/></svg>Consequuntur magni dolores eos qui ratione</li>
      <li><svg><use href="#tick"/></svg>Voluptatem sequi nesciunt.</li>
      <li><svg><use href="#tick"/></svg>Neque porro quisquam est, qui dolorem</li>
      <li><svg><use href="#tick"/></svg>Ipsum quia dolor sit amet, consectetu</li>
      <li><svg><use href="#tick"/></svg>Aadipisci velit, sed quia non numquam</li>
    </ul>
    <span class="page-no">04</span>
  </section>

  <!-- Slide 08: content with image left -->
  <section class="slide col-b row-4">
    <h2 class="tab w-wide">OUR CHALLENGES</h2>
    <div class="figure photo-help" style="left:9px; top:42px; width:192px; height:190px" role="img" aria-label="Hand reaching down to help a hiker climb a rock at sunrise"></div>
    <div class="text-col" style="left:220px; top:20px">
      <p class="copy">Sed ut perspiciatis unde omnis iste natus error sit voluptatem accusantium doloremque laudantium, totam rem aperiam, eaque ipsa quae ab illo inventore veritatis et quasi architecto beatae vitae dicta sunt explicabo. Nemo enim ipsam voluptatem quia voluptas sit aspernatur aut odit aut fugit, sed quia consequuntur magni dolores eos qui ratione voluptatem sequi nesciunt. Neque porro quisquam est, qui dolorem ipsum quia dolor sit amet, consectetur, adipisci velit, sed quia non numquam eius modi tempora incidunt ut labore et dolore magnam aliquam quaerat voluptatem. Ut enim ad minima veniam, quis nostrum exercitationem ullam corporis suscipit laboriosam, nisi ut aliquid ex ea commodi consequatur</p>
      <p class="copy">Sed ut perspiciatis unde omnis iste natus error sit voluptatem accusantium doloremque laudantium, totam rem aperiam, eaque ipsa quae ab illo inventore veritatis et quasi architecto beatae vitae dicta sunt explicabo. Nemo enim ipsam voluptatem quia voluptas sit aspernatur aut odit aut fugit, sed quia consequuntur magni dolores eos qui ratione voluptatem sequi nesciunt. Neque porro quisquam est, qui dolorem ipsum quia dolor sit amet, consectetur, adipisci velit, sed quia non numquam eius modi tempora incidunt ut labore et dolore magnam aliquam quaerat voluptatemt enim ad minima veniam, quis nostrum exercitationem ullam corporis suscipit laboriosam, nisi ut aliquid ex ea commodi consequatur</p>
    </div>
    <span class="page-no">08</span>
  </section>

</main>
</body>
</html>
```